Healthy lifestyle Influencer business card

I need your creativity to have a business card that I can leave in all the restaurants, hotels and spas I visit to inform them that I am an influencer specializing in the wellness sector and that I will write a review about them. You can use my instagram photos Lunavita27 or on my website www.piattileggeriorto.it. I would like my business card to impress with its creativity! thank you very much!

Contact Information for Business Card

siteweb, instagram, phone number

Font styles to use
Decorative
Script

Colors
0094D4
00A9DD
6FCCEA
C7EBF8
E9F6FB
59FF00
82FF00
B8FF75
E3FFCB
F4FFEA
FFC000
F8CF3A
FAE287
FDF2CF
FEFAEE
F0912C
F2A743
F7CA91
FBE8D2
FDF5EE
EE7325
F08F49
F5BC92
FAE3D3
FDF4ED
EB3D1F
EC4F4E
F09395
F8D3D4
FCEDEE
E54698
E96AAD
F1A4CE
F9D9EA
FCEFF6

Requirements
Nice to have
• creativity

```html
<!DOCTYPE html>
<html lang="it">
<head>
<meta charset="utf-8">
<title>Tavola Serena – biglietto da visita</title>
<link rel="stylesheet" href="https://fonts.googleapis.com/css2?family=Great+Vibes&family=Roboto:wght@400&display=swap">
<style>
  :root {
    --backdrop: #2a2a2b;
    --card-top: #18191a;
    --card-bottom: #2d2e30;
    --ink-light: #e6e8e9;
    --ink-soft: #c9cccf;
    --ink-emboss: #121314;
    --dot: #6fccea;
  }
  * { margin: 0; padding: 0; box-sizing: border-box; }
  html, body {
    width: 1200px; height: 1138px; overflow: hidden;
    background: var(--backdrop);
    font-family: "Roboto", Arial, sans-serif;
  }
  .sheet { position: relative; width: 1200px; height: 1138px; }
  .card {
    position: absolute;
    width: 620px; height: 376px;
    border-radius: 16px;
    background: linear-gradient(160deg, var(--card-top) 0%, var(--card-bottom) 100%);
  }
  .card--front { left: 272px; top: 184px; }
  .card--back { left: 274px; top: 606px; }

  .brand { position: absolute; text-align: center; font-weight: 400; }
  .brand__name { display: block; line-height: 1; white-space: nowrap; }
  .brand__tagline { display: block; line-height: 1; white-space: nowrap; }

  .card--front .brand { left: 0; right: 0; top: 148px; color: var(--ink-emboss); }
  .card--front .brand__name { font-size: 54px; letter-spacing: 1px; }
  .card--front .brand__tagline { font-size: 22px; margin-top: 22px; }

  .social {
    position: absolute; display: flex; align-items: center; gap: 12px;
    color: var(--ink-light); font-size: 17px;
  }
  .social__dot { width: 14px; height: 14px; border-radius: 50%; background: var(--dot); }
  .card--front .social { left: 0; right: 0; top: 335px; justify-content: center; }

  .holder {
    position: absolute; left: 22px; top: 44px;
    font-family: "Great Vibes", cursive; font-size: 42px;
    color: var(--ink-light); font-weight: 400;
  }
  .contacts { position: absolute; left: 28px; top: 216px; list-style: none; }
  .contacts li {
    display: flex; align-items: center; gap: 9px;
    height: 21px; font-size: 14.5px; color: var(--ink-soft);
  }
  .contacts svg { width: 14px; height: 14px; fill: var(--ink-soft); }
  .vat { position: absolute; left: 28px; top: 285px; font-size: 14.5px; color: var(--ink-soft); }
  .card--back .social { left: 28px; top: 322px; }

  .card--back .brand { left: 292px; width: 300px; top: 270px; color: var(--ink-light); }
  .card--back .brand__name { font-size: 38px; }
  .card--back .brand__tagline { font-size: 16px; margin-top: 14px; }
</style>
</head>
<body>
<main class="sheet">
  <section class="card card--front" aria-label="Fronte del biglietto">
    <div class="brand">
      <span class="brand__name">Tavola Serena</span>
      <span class="brand__tagline">Benessere in ogni assaggio</span>
    </div>
    <div class="social">
      <span class="social__dot"></span>
      <span>@Lunavita27</span>
    </div>
  </section>

  <section class="card card--back" aria-label="Retro del biglietto">
    <h1 class="holder">Luna Moretti</h1>
    <ul class="contacts">
      <li>
        <svg viewBox="0 0 16 16" aria-hidden="true"><path d="M1 6c0-2 3-3 7-3s7 1 7 3v1h-3V5.5C11 5 9.5 5 8 5s-3 0-4 .5V7H1zM4 8h8l2 5H2z"/></svg>
        <span>000-0000-0000</span>
      </li>
      <li>
        <svg viewBox="0 0 16 16" aria-hidden="true"><path d="M1 3h14v10H1zm1.5 1.5v.3L8 9l5.5-4.2v-.3zm0 2.2v4.8h11V6.7L8 10.8z"/></svg>
        <span>info@piattileggeriorto.it</span>
      </li>
      <li>
        <svg viewBox="0 0 16 16" aria-hidden="true"><path d="M8 1a7 7 0 100 14A7 7 0 008 1zm-1 1.8V7H3a5.2 5.2 0 014-4.2zm2 0A5.2 5.2 0 0113 7H9zM3 9h4v4.2A5.2 5.2 0 013 9zm6 0h4a5.2 5.2 0 01-4 4.2z"/></svg>
        <span>www.piattileggeriorto.it</span>
      </li>
    </ul>
    <p class="vat">Partita IVA 04512390176</p>
    <div class="social">
      <span class="social__dot"></span>
      <span>@Lunavita27</span>
    </div>
    <div class="brand">
      <span class="brand__name">Tavola Serena</span>
      <span class="brand__tagline">Benessere in ogni assaggio</span>
    </div>
  </section>
</main>
</body>
</html>
```